q-zen design for startup inpection service

building and pest inspections what i had in mind was q-zen in large print with prepurchase in small print directly under it and the small tm (tradmark) .Within the C I would like an eye but I don't want to take away from the C so maybe the eye would be done in a fine line?I would also like the Building and Pest inspections to be prominent and large .Have no idea of colors but do like black orange and silver

Target Market(s)

home buyers and realestate agents

Industry/Entity Type

Building

Contact Information for Business Card

q-zen prepurchase, Phone 0412093816, fax 02 71934058, email q-zen@mailbrook.com.au ,building and pest inspections

Font styles to use
Sans Serif

Requirements
Must have
• bold color
• simple layout
• bold color
• uncluttered layout
Should not have
• contact details the same size as Building and Pest Inspections

```html
<!DOCTYPE html>
<html lang="en">
<head>
<meta charset="utf-8">
<title>q-zen prepurchase business card</title>
<link rel="stylesheet" href="https://fonts.googleapis.com/css2?family=Roboto:wght@300;400;700&display=swap">
<style>
  :root {
    --page-bg: #e4e4e2;
    --card-black: #050505;
    --name-silver: #cfd0d2;
    --brand-blue: #3f86c7;
    --band-text: #e3edf7;
    --divider: #2a2a2a;
  }
  html, body {
    margin: 0;
    padding: 0;
    width: 1200px;
    height: 848px;
    overflow: hidden;
    background: var(--page-bg);
    font-family: "Roboto", Arial, sans-serif;
  }
  .business-card {
    position: absolute;
    left: 100px;
    top: 138px;
    width: 1000px;
    height: 572px;
    border-radius: 40px;
    background: var(--card-black);
    overflow: hidden;
    box-shadow: 0 18px 40px rgba(0,0,0,0.22);
  }
  .business-name {
    position: absolute;
    left: 64px;
    top: 170px;
    width: 520px;
    margin: 0;
    font-weight: 400;
    font-size: 58px;
    line-height: 1.1;
    color: var(--name-silver);
    white-space: nowrap;
  }
  .divider {
    position: absolute;
    left: 612px;
    top: 0;
    width: 1px;
    height: 410px;
    background: var(--divider);
  }
  .contact-list {
    position: absolute;
    right: 58px;
    top: 196px;
    margin: 0;
    padding: 0;
    list-style: none;
  }
  .contact-item {
    display: flex;
    justify-content: flex-end;
    align-items: center;
    gap: 18px;
    height: 34px;
    font-weight: 300;
    font-size: 25px;
    color: var(--brand-blue);
  }
  .contact-icon {
    width: 20px;
    height: 20px;
    fill: var(--brand-blue);
    flex: none;
  }
  .service-band {
    position: absolute;
    left: 0;
    right: 0;
    bottom: 0;
    height: 162px;
    background: var(--brand-blue);
    display: flex;
    align-items: center;
    justify-content: center;
  }
  .service-line {
    margin: 0;
    font-weight: 300;
    font-size: 46px;
    color: var(--band-text);
    letter-spacing: 0.3px;
  }
</style>
</head>
<body>
  <section class="business-card">
    <h1 class="business-name">q-zen prepurchase</h1>

    <div class="divider"></div>

    <ul class="contact-list">
      <li class="contact-item">
        <span>0412093816</span>
        <svg class="contact-icon" viewBox="0 0 24 24" aria-label="phone"><path d="M6.6 10.8c1.4 2.8 3.8 5.1 6.6 6.6l2.2-2.2c.3-.3.7-.4 1-.2 1.1.4 2.3.6 3.6.6.6 0 1 .4 1 1V20c0 .6-.4 1-1 1C10.6 21 3 13.4 3 4c0-.6.4-1 1-1h3.5c.6 0 1 .4 1 1 0 1.3.2 2.5.6 3.6.1.3 0 .7-.2 1z"/></svg>
      </li>
      <li class="contact-item">
        <span>02 71934058</span>
        <svg class="contact-icon" viewBox="0 0 24 24" aria-label="fax"><path d="M6 2h12v5H6z"/><path d="M3 8h18a2 2 0 0 1 2 2v7h-4v-3H5v3H1v-7a2 2 0 0 1 2-2z"/><path d="M6 15h12v7H6z"/></svg>
      </li>
      <li class="contact-item">
        <span>q-zen@mailbrook.com.au</span>
        <svg class="contact-icon" viewBox="0 0 24 24" aria-label="email"><path d="M2 5h20v14H2zM4 7v.4l8 5.6 8-5.6V7z" fill-rule="evenodd"/></svg>
      </li>
    </ul>

    <div class="service-band">
      <p class="service-line">building and pest inspections</p>
    </div>
  </section>
</body>
</html>
```